Traineeship Flyer Design Project

Requirements:
• 1 x A4 page flyer (double sided)
1st page; target market 15-19 yr old, looking for young/fresh, exciting, eye catching
2nd page: same look/feel – target market – parents/person to determine if there is value to devoting energy to this qualification (potentially less busy in design)
• Use of high quality logos: 1. Valtrexo 2. Nationally recognised training logo
Ideally wanting to keep amount of copy to the page layout as attached, although designer is free to interpret the layout of copy on each page, although Valtrexo will accept alternative presentation if designer sees new way to combine information
• Valtrexo does not have a set colour palette so there are no restrictions/guidelines to follow
Updates
Hi, All files including brief and logos have now been updated.
Reason: Hi everyone
Please refer to design submission below for the only design that was deemed to cover off on the brief as the starting point - in regards to producing a design that appeals to target market of young person (15-19) in regards to self selecting to take up further study
Hi everyone
Can you please view the 3 remaining designs that are in contention (out of 30+ submitted) - Design 1528020 ; 1510098; 1510087; I will be providing additional feedback to these designers, as that come closer to the mark of appealing to younger "potential trainee" - the collateral needs to make the young student want to pick up the flyer (eye catching/interesting) and then be motivated to want to self elect - "beg parents" to take up the option. **PLEASE NOTE - I have uploaded a colour swatch now, and would appreciate if desgins could use these colours (not a requirement to use base colours of blue a silver as base if an exciting image needs to come from leaning on "secondary colours" (brighter) as being the predominant colours.
Many thanks, appreciate being able to see such an active community of designers involved in this website
Target Market(s)
1st page; target market 15-19 yr old, looking for young/fresh, exciting, eye catching. same look/feel – target market – parents/person to decide on
Industry/Entity Type
Training
Look and feel

```html
<!DOCTYPE html>
<html lang="en">
<head>
<meta charset="utf-8">
<title>Valtrexo Traineeship Flyer</title>
<link href="https://fonts.googleapis.com/css2?family=Courgette&family=Kurale&family=Roboto:wght@400;700&display=swap" rel="stylesheet">
<style>
  :root {
    --navy: #1f2366;
    --ink: #26297a;
    --text: #4a4a4a;
    --paper: #f4f4f4;
    --circle: #d6d6d6;
    --circle-edge: #c4c4c4;
    --step1: #7d8a2b;
    --step2: #98792a;
    --step3: #a2262d;
    --step4: #5a2d91;
    --step5: #23903f;
    --step6: #2b86b0;
    --rule: #8a8fc0;
  }
  * { box-sizing: border-box; margin: 0; padding: 0; }
  html, body { width: 1200px; height: 800px; overflow: hidden; background: #e4e4e4; }
  .flyer {
    position: relative; width: 1200px; height: 800px;
    background: var(--paper); font-family: "Roboto", Arial, sans-serif; color: var(--text);
  }
  .masthead {
    position: absolute; top: 0; left: 0; width: 1200px; height: 190px; background: var(--navy);
  }
  .masthead-photo {
    position: absolute; top: 14px; left: 20px; width: 440px; height: 162px;
    border: 4px solid #fff; background: linear-gradient(120deg, #6d6a5e, #a08a52 45%, #4d5d7a);
  }
  .masthead-title {
    position: absolute; top: 40px; left: 500px; right: 40px;
    color: #eef0f8; font-weight: 700; font-size: 40px; line-height: 1.15; text-align: center;
  }
  .steps {
    position: absolute; top: 205px; left: 30px; right: 30px;
    display: flex; justify-content: space-between; align-items: flex-start;
  }
  .step { display: flex; flex-direction: column; align-items: center; width: 150px; position: relative; }
  .step-circle {
    width: 120px; height: 96px; border-radius: 50%; background: var(--circle);
    border: 1px solid var(--circle-edge);
    display: flex; align-items: center; justify-content: center; text-align: center;
    font-family: "Kurale", Georgia, serif; font-size: 16px; color: #555; line-height: 1.1;
  }
  .step-tag {
    margin-top: 8px; width: 120px; height: 22px; border-radius: 4px; color: #fff;
    font-family: "Kurale", Georgia, serif; font-style: italic; font-size: 14px;
    display: flex; align-items: center; justify-content: center;
  }
  .step-arrow { position: absolute; right: -10px; top: 36px; font-size: 20px; color: #666; }
  .headline {
    position: absolute; top: 352px; left: 40px; right: 40px;
    font-weight: 700; font-size: 29px; color: #3b3b3b;
  }
  .section { position: absolute; left: 40px; right: 40px; }
  .section-heading {
    font-family: "Courgette", cursive; color: var(--ink); font-size: 30px;
    border-bottom: 1px solid var(--rule); padding-bottom: 2px;
  }
  .section-body { font-size: 20px; margin-top: 8px; }
  .cost { top: 400px; }
  .duties { top: 492px; }
  .duties-row { display: flex; align-items: center; gap: 20px; margin-top: 8px; }
  .tick-list { list-style: none; font-size: 18px; line-height: 1.6; }
  .tick-list li { display: flex; align-items: center; gap: 10px; }
  .tick-list svg { width: 16px; height: 16px; }
  .duties-note { font-size: 22px; }
  .duration { top: 680px; }
  .footer-band { position: absolute; bottom: 0; left: 0; width: 1200px; height: 14px; background: var(--navy); }
</style>
</head>
<body>
<div class="flyer">
  <header class="masthead">
    <div class="masthead-photo" role="img" aria-label="Photo of a trainee operating heavy machinery with a supervisor"></div>
    <h1 class="masthead-title">Get ahead.<br>Learn on the job.</h1>
  </header>

  <section class="steps">
    <div class="step"><div class="step-circle">Information<br>session</div><div class="step-tag" style="background:var(--step1)">Step 01</div><span class="step-arrow">›</span></div>
    <div class="step"><div class="step-circle">Register<br>your<br>interest</div><div class="step-tag" style="background:var(--step2)">Step 02</div><span class="step-arrow">›</span></div>
    <div class="step"><div class="step-circle">Enrolment</div><div class="step-tag" style="background:var(--step3)">Step 03</div><span class="step-arrow">›</span></div>
    <div class="step"><div class="step-circle">Start<br>training</div><div class="step-tag" style="background:var(--step4)">Step 04</div><span class="step-arrow">›</span></div>
    <div class="step"><div class="step-circle">Practical<br>assessments</div><div class="step-tag" style="background:var(--step5)">Step 05</div><span class="step-arrow">›</span></div>
    <div class="step"><div class="step-circle">Graduate</div><div class="step-tag" style="background:var(--step6)">Step 06</div></div>
  </section>

  <p class="headline">Gain a formal national qualification recognised by all employers Australia wide.</p>

  <section class="section cost">
    <h2 class="section-heading">How much will it cost?</h2>
    <p class="section-body">Nothing! The full course is provided by your employer. No prior training/experience is required.</p>
  </section>

  <section class="section duties">
    <h2 class="section-heading">What would I be expected to do?</h2>
    <div class="duties-row">
      <ul class="tick-list">
        <li><svg viewBox="0 0 16 16"><path d="M2 9l4 4 8-10" fill="none" stroke="#555" stroke-width="2"/></svg>Earn while your learn</li>
        <li><svg viewBox="0 0 16 16"><path d="M2 9l4 4 8-10" fill="none" stroke="#555" stroke-width="2"/></svg>Attend on site training sessions</li>
        <li><svg viewBox="0 0 16 16"><path d="M2 9l4 4 8-10" fill="none" stroke="#555" stroke-width="2"/></svg>Online training and assessment</li>
        <li><svg viewBox="0 0 16 16"><path d="M2 9l4 4 8-10" fill="none" stroke="#555" stroke-width="2"/></svg>Complete workplace activities</li>
      </ul>
      <svg width="40" height="120" viewBox="0 0 40 120" aria-hidden="true"><path d="M4 4 Q22 4 22 30 L22 50 Q22 60 36 60 Q22 60 22 70 L22 90 Q22 116 4 116" fill="none" stroke="#333" stroke-width="2"/></svg>
      <p class="duties-note">All training completed during work hours.</p>
    </div>
  </section>

  <section class="section duration">
    <h2 class="section-heading">How long will it take to finish my traineeship?</h2>
    <p class="section-body">On track, you could complete a Cert II in 6 months if you are committed to making your training a priority.</p>
  </section>

  <div class="footer-band"></div>
</div>
</body>
</html>
```